Life Coaching Business Card

Please check out my website at www.lorettavanbrekel.example. Ideally I would like to use the same colors that I used on the site to match my business cards i.e: pink, green, teal, white
I want the final design to include a picture of me and also to be appealing and eye catching. For the picture I submitted, you can crop it smaller to just have my face (exclude my chest) showing.
Business
Contact Information for Business Card
Loretta Vanbrekel
Transformational Life Coach
web: www.lorettavanbrekel.example
email: loretta@lorettavanbrekel.example
Phone: 555-318-7062

```html
<!DOCTYPE html>
<html lang="en">
<head>
<meta charset="utf-8">
<title>Loretta Vanbrekel – Business Card</title>
<link rel="stylesheet" href="https://fonts.googleapis.com/css2?family=Abril+Fatface&family=Open+Sans:wght@400;600&family=Cinzel:wght@700&family=Tinos&display=swap">
<style>
  :root {
    --magenta: #ff17e6;
    --lavender: #e8c4ec;
    --lavender-line: #f2dcf4;
    --divider: #c41ab4;
    --green: #8bd33e;
    --green-light: #9adb52;
    --green-line: #b7e68a;
    --gold-start: #c9a64a;
    --gold-end: #f4e2b5;
    --white: #ffffff;
    --ink: #1a1a1a;
    --photo-dark: #3a3a3a;
    --photo-mid: #9a9a9a;
  }
  * { margin: 0; padding: 0; box-sizing: border-box; }
  html, body { width: 940px; height: 1200px; overflow: hidden; background: var(--white); }
  .canvas { position: relative; width: 940px; height: 1200px; }

  .card { position: absolute; left: 75px; width: 790px; height: 465px; background: var(--magenta); overflow: hidden; }
  .card--front { top: 75px; }
  .card--back { top: 583px; }

  .portrait {
    position: absolute; left: 0; top: 0; width: 290px; height: 465px;
    background: linear-gradient(90deg, var(--photo-dark) 0%, var(--photo-mid) 45%, #d9d9d9 75%, rgba(255,23,230,0) 100%);
  }
  .name-band {
    position: absolute; left: 198px; top: 122px; width: 592px; height: 85px;
    background: linear-gradient(90deg, rgba(255,255,255,0.55) 0%, #fff 15%, #fde6fb 70%, rgba(255,255,255,0.3) 100%);
  }
  .name {
    position: absolute; left: 207px; top: 126px;
    font-family: 'Abril Fatface', serif; font-size: 57px; line-height: 1; color: var(--ink);
    letter-spacing: 0.5px;
  }
  .title-bar {
    position: absolute; left: 207px; top: 231px; width: 451px; height: 38px;
    background: linear-gradient(90deg, var(--gold-start) 0%, #dcbf72 55%, var(--gold-end) 100%);
  }
  .title {
    position: absolute; left: 216px; top: 234px;
    font-family: 'Open Sans', sans-serif; font-size: 25px; letter-spacing: 1.5px; color: var(--white);
  }
  .website {
    position: absolute; left: 288px; top: 283px;
    font-family: 'Tinos', serif; font-size: 24px; color: var(--white);
  }

  .icon-column { position: absolute; left: 137px; top: 0; width: 104px; height: 465px; background: var(--lavender); }
  .column-divider { position: absolute; left: 241px; top: 0; width: 5px; height: 465px; background: var(--divider); }
  .contact-panel { position: absolute; left: 246px; top: 0; width: 405px; height: 465px; }
  .contact-row {
    position: absolute; left: 0; width: 405px; height: 116px;
    background: linear-gradient(180deg, var(--green-light), var(--green));
    border-top: 2px solid var(--green-line);
    display: flex; align-items: center; padding-left: 30px;
    font-family: 'Open Sans', sans-serif; font-size: 20px; color: var(--white);
  }
  .contact-row::before {
    content: ""; display: inline-block; margin-right: 12px;
    border-left: 7px solid var(--ink); border-top: 5px solid transparent; border-bottom: 5px solid transparent;
  }
  .contact-row--name { font-family: 'Cinzel', serif; font-weight: 700; font-size: 23px; letter-spacing: 0.5px; border-top: none; }
  .row-icons { position: absolute; left: 137px; top: 0; }
  .row-lines { position: absolute; left: 137px; top: 0; }
</style>
</head>
<body>
<div class="canvas">
  <section class="card card--front">
    <div class="portrait" role="img" aria-label="Portrait photo of Loretta Vanbrekel"></div>
    <div class="name-band"></div>
    <h1 class="name">Loretta Vanbrekel</h1>
    <div class="title-bar"></div>
    <p class="title">TRANSFORMATIONAL LIFE COACH</p>
    <p class="website">www.lorettavanbrekel.example</p>
  </section>

  <section class="card card--back">
    <div class="icon-column"></div>
    <svg class="row-lines" width="104" height="465" viewBox="0 0 104 465" aria-hidden="true">
      <g stroke="#f2dcf4" stroke-width="2">
        <line x1="0" y1="116" x2="104" y2="116"/>
        <line x1="0" y1="232" x2="104" y2="232"/>
        <line x1="0" y1="348" x2="104" y2="348"/>
      </g>
    </svg>
    <svg class="row-icons" width="104" height="465" viewBox="0 0 104 465" aria-hidden="true">
      <g fill="#dcaee2">
        <circle cx="52" cy="48" r="11"/>
        <path d="M32 78 Q52 56 72 78 Z"/>
        <rect x="34" y="160" width="36" height="24" rx="2"/>
        <path d="M34 160 L52 174 L70 160" stroke="#eacdee" stroke-width="2" fill="none"/>
        <ellipse cx="52" cy="284" rx="19" ry="14"/>
        <path d="M42 294 L38 306 L52 296 Z"/>
        <path d="M34 418 Q30 404 42 402 Q46 390 58 394 Q70 392 70 404 Q78 406 74 418 Z"/>
      </g>
    </svg>
    <div class="column-divider"></div>
    <div class="contact-panel">
      <p class="contact-row contact-row--name" style="top:0">LORETTA VANBREKEL</p>
      <p class="contact-row" style="top:116px">555-318-7062</p>
      <p class="contact-row" style="top:232px">loretta@lorettavanbrekel.example</p>
      <p class="contact-row" style="top:348px;height:117px">www.lorettavanbrekel.example</p>
    </div>
  </section>
</div>
</body>
</html>
```